Velvo Dairy Macadamia and Rosella Eco Pouch Product Launch Adverts

We require an Advert to use across socials to announce this new product. Ideally we would like the concept to be resized to work as a banner ad, display ad and Carosel advert for Zentrix, Plumora, Clipnest and Vistagrove. I have attached the assets if you are interested in this job including colourstyle guide, pervious campaigns, fonts and logos.

```html
<!DOCTYPE html>
<html lang="en">
<head>
<meta charset="utf-8">
<title>Lunel Botanics Eco Pouch Launch Adverts</title>
<link href="https://fonts.googleapis.com/css2?family=Zilla+Slab:ital,wght@0,300;0,400;0,600;1,300&display=swap" rel="stylesheet">
<style>
:root{
  --peach:#f6c6b3;
  --rose:#e9b7b0;
  --sand:#ead9c8;
  --stone:#d8d7d6;
  --ink:#1d1a1a;
  --cocoa:#7a625d;
  --white:#ffffff;
  --label:#8a8a8a;
  --pouch:#fbf7f5;
  --lilac:#eed3de;
}
*{margin:0;padding:0;box-sizing:border-box}
html,body{width:1200px;height:1085px;overflow:hidden;background:#fff}
body{position:relative;font-family:"Zilla Slab",Georgia,serif;font-weight:300}
.group-title{position:absolute;font-size:7px;font-weight:600;color:var(--ink)}
.size{position:absolute;font-size:3.5px;color:var(--label)}
.ad{position:absolute;overflow:hidden;color:var(--white);text-align:center}
.ad.peach{--base:var(--peach);background:var(--peach)}
.ad.rose{--base:var(--rose);background:var(--rose)}
.ad.sand{--base:var(--sand);background:var(--sand)}
.ad.stone{--base:var(--stone);background:var(--stone)}
.photo{
  position:absolute;inset:0;
  background:
    radial-gradient(ellipse var(--rw,30%) var(--rh,40%) at var(--cx,50%) var(--cy,62%),
      var(--pouch) 0, var(--pouch) 35%, var(--lilac) 70%, rgba(238,211,222,0) 100%),
    var(--base);
}
.photo.nuts{
  background:
    radial-gradient(ellipse var(--rw,30%) var(--rh,40%) at var(--cx,50%) var(--cy,62%),
      var(--pouch) 0, var(--pouch) 35%, var(--lilac) 70%, rgba(238,211,222,0) 100%),
    linear-gradient(180deg, var(--base) 0, var(--base) 72%, #ecc897 100%);
}
.copy{position:absolute;line-height:1.18}
.headline{font-style:italic;font-weight:300}
.mark{position:absolute;font-weight:600;color:var(--ink);line-height:1}
.mark.light{color:var(--white)}
.brand{font-weight:600;letter-spacing:.4px;text-transform:uppercase;line-height:1.1}
.brand small{display:block;font-size:.4em;font-weight:400;letter-spacing:.3px}
.cocoa{color:var(--cocoa)}
.dark{color:var(--ink)}
.left{text-align:left}
</style>
</head>
<body>

<!-- Zentrix display network -->
<div class="group-title" style="left:489px;top:17px">Zentrix</div>

<div class="size" style="left:27px;top:38px">300x100</div>
<div class="ad peach" style="left:20px;top:46px;width:74px;height:24px">
  <div class="photo" role="img" aria-label="Refill pouch on white blocks" style="--cx:22%;--rw:14%;--rh:45%"></div>
  <div class="copy dark left" style="left:38px;top:3px;width:34px;font-size:2.6px"><i>1 Cream = 6 uses</i><br>including reducing rosacea and hyperpigmentation, hand cream, night cream, heel balm</div>
</div>

<div class="size" style="left:104px;top:38px">728x90</div>
<div class="ad peach" style="left:101px;top:46px;width:179px;height:22px">
  <div class="photo" role="img" aria-label="Refill pouch on white blocks" style="--cx:12%;--rw:7%;--rh:50%"></div>
  <div class="copy" style="left:45px;top:5px;width:110px;font-size:4.4px">Environmentally friendly coated<br>craft recycled paper with aluminium lining</div>
  <div class="mark light" style="right:4px;top:7px;font-size:7px">Lunel</div>
</div>

<div class="size" style="left:27px;top:77px">468x60</div>
<div class="ad peach" style="left:20px;top:84px;width:115px;height:14px">
  <div class="photo" role="img" aria-label="Refill pouch" style="--cx:12%;--rw:7%;--rh:55%"></div>
  <div class="mark light" style="left:30px;top:4px;font-size:5.5px">Lunel</div>
  <div class="copy" style="left:50px;top:2px;width:64px;font-size:3.8px">Lunel's Indulgent,<br>luxuriousness, Velvo Dairy</div>
</div>

<div class="size" style="left:142px;top:77px">120x90</div>
<div class="ad stone" style="left:140px;top:84px;width:30px;height:22px">
  <div class="photo" role="img" aria-label="Refill pouch held in hand" style="--cx:25%;--rw:22%;--rh:50%"></div>
  <div class="copy dark" style="left:13px;top:3px;width:16px;font-size:2.6px">Eco Pouch =<br>3 Refills</div>
</div>

<div class="size" style="left:27px;top:103px">720x300</div>
<div class="ad sand" style="left:20px;top:110px;width:177px;height:74px">
  <div class="photo" role="img" aria-label="Hands squeezing cream from refill pouch" style="--cx:17%;--cy:55%;--rw:20%;--rh:55%"></div>
  <div class="copy brand" style="left:70px;top:12px;width:96px;font-size:6.6px">Lunel Botanics<small>Native Garden Remedies</small></div>
  <div class="copy cocoa" style="left:70px;top:25px;width:96px;font-size:5.6px">Wonder miracle cream, comes with a washable silicone refillable tube.</div>
  <div class="mark light" style="left:70px;width:96px;top:55px;font-size:7px">Lunel</div>
</div>

<div class="size" style="left:205px;top:103px">120x240</div>
<div class="ad stone" style="left:203px;top:110px;width:29px;height:59px">
  <div class="photo" role="img" aria-label="Refill pouch against stone" style="--cy:65%;--rw:38%;--rh:35%"></div>
  <div class="copy" style="left:1px;top:3px;width:27px;font-size:3px">1 eco pouch =<br>3 Refills</div>
</div>

<div class="size" style="left:240px;top:103px">300x250</div>
<div class="ad rose" style="left:238px;top:110px;width:74px;height:61px">
  <div class="photo nuts" role="img" aria-label="Refill pouch with macadamia nuts" style="--cx:72%;--cy:58%;--rw:20%;--rh:42%"></div>
  <div class="copy left" style="left:4px;top:4px;width:24px;font-size:2.8px">Environmentally friendly coated craft recycled paper with aluminium lining</div>
  <div class="copy brand" style="left:42px;top:5px;width:30px;font-size:3px">Lunel Botanics</div>
  <div class="mark" style="left:4px;top:45px;font-size:6px">Lunel</div>
</div>

<div class="size" style="left:323px;top:38px">300x600</div>
<div class="ad peach" style="left:317px;top:46px;width:74px;height:147px">
  <div class="photo" role="img" aria-label="Refill pouch on white blocks" style="--cy:68%;--rw:32%;--rh:26%"></div>
  <div class="copy" style="left:3px;top:10px;width:68px;font-size:6px;font-weight:600">1 Cream = 6 uses</div>
  <div class="copy" style="left:4px;top:20px;width:66px;font-size:3.7px">including reducing rosacea and hyperpigmentation, hand cream, night cream, heel + elbow balm, nipple cream, nappy cream</div>
  <div class="mark" style="left:5px;top:139px;font-size:4.5px">Lunel</div>
</div>

<div class="size" style="left:401px;top:38px">160x600</div>
<div class="ad sand" style="left:398px;top:46px;width:39px;height:147px">
  <div class="photo" role="img" aria-label="Hands holding refill pouch" style="--cy:48%;--rw:45%;--rh:20%"></div>
  <div class="mark light" style="left:0;width:39px;top:12px;font-size:8px">Lunel</div>
  <div class="copy cocoa headline" style="left:2px;top:104px;width:35px;font-size:3.8px">Wonder miracle cream, comes with a washable silicone refillable tube.</div>
  <div class="copy brand" style="left:0;width:39px;top:132px;font-size:3.6px">Lunel Botanics</div>
</div>

<div class="size" style="left:446px;top:38px">120x600</div>
<div class="ad stone" style="left:443px;top:46px;width:30px;height:147px">
  <div class="photo" role="img" aria-label="Refill pouch against stone" style="--cy:45%;--rw:40%;--rh:18%"></div>
  <div class="copy headline cocoa left" style="left:3px;top:10px;width:26px;font-size:3.4px">Lunel's Indulgent, luxuriousness, Velvo Dairy</div>
  <div class="mark" style="left:0;width:30px;top:103px;font-size:6px">Lunel</div>
  <div class="copy dark" style="left:1px;top:120px;width:28px;font-size:2.5px">Environmentally friendly coated craft recycled paper with aluminium lining</div>
</div>

<div class="size" style="left:493px;top:38px">336x280</div>
<div class="ad sand" style="left:487px;top:46px;width:82px;height:69px">
  <div class="photo" role="img" aria-label="Hands with refill pouch and cream" style="--cx:38%;--cy:45%;--rw:38%;--rh:45%"></div>
  <div class="mark light" style="left:4px;top:4px;font-size:5px">Lunel</div>
  <div class="copy left" style="left:6px;top:57px;width:76px;font-size:5px">1 eco pouch = 3 Refills</div>
</div>

<div class="size" style="left:578px;top:38px">320x50</div>
<div class="ad peach" style="left:575px;top:46px;width:79px;height:13px">
  <div class="photo" role="img" aria-label="Refill pouch" style="--cx:14%;--rw:10%;--rh:55%"></div>
  <div class="copy" style="left:25px;top:2px;width:45px;font-size:2.6px">Environmentally friendly coated craft recycled paper with aluminium lining</div>
</div>

<div class="size" style="left:578px;top:65px">200x200</div>
<div class="ad peach" style="left:575px;top:72px;width:49px;height:49px">
  <div class="photo" role="img" aria-label="Refill pouch on white blocks" style="--cx:35%;--cy:68%;--rw:25%;--rh:32%"></div>
  <div class="copy dark" style="left:2px;top:4px;width:45px;font-size:2.8px">Lunel's Indulgent,<br>luxuriousness, Velvo Dairy</div>
</div>

<div class="size" style="left:661px;top:38px">250x250</div>
<div class="ad rose" style="left:659px;top:46px;width:62px;height:62px">
  <div class="photo nuts" role="img" aria-label="Refill pouch with macadamia nuts" style="--cx:32%;--cy:45%;--rw:25%;--rh:40%"></div>
  <div class="copy left" style="left:42px;top:12px;width:18px;font-size:2.7px">Wonder miracle cream, comes with a washable silicone refillable tube.</div>
  <div class="mark" style="left:3px;top:56px;font-size:3.5px">Lunel</div>
</div>

<!-- Clipnest -->
<div class="group-title" style="left:28px;top:208px">Clipnest</div>

<div class="size" style="left:28px;top:227px">1000x1500</div>
<div class="ad peach" style="left:20px;top:236px;width:246px;height:368px">
  <div class="photo" role="img" aria-label="Refill pouch standing against white blocks" style="--cx:42%;--cy:82%;--rw:18%;--rh:16%"></div>
  <div class="copy brand" style="left:0;width:246px;top:36px;font-size:8.5px">Lunel Botanics<small>Native Garden Remedies</small></div>
  <div class="copy headline cocoa" style="left:0;width:246px;top:54px;font-size:27px">1 Cream = 6 uses</div>
  <div class="copy" style="left:18px;width:210px;top:90px;font-size:12px;line-height:14px">including reducing rosacea and hyperpigmentation, hand cream, night cream, heel + elbow balm, nipple cream, nappy cream</div>
  <div class="mark" style="left:0;width:246px;top:168px;font-size:34px">Lunel</div>
</div>

<div class="size" style="left:28px;top:616px">1000x1000</div>
<div class="ad peach" style="left:20px;top:625px;width:246px;height:246px">
  <div class="photo" role="img" aria-label="Refill pouch with cream at spout" style="--cx:48%;--cy:100%;--rw:34%;--rh:34%"></div>
  <div class="mark" style="left:0;width:246px;top:24px;font-size:24px">Lunel</div>
  <div class="copy" style="left:0;width:246px;top:55px;font-size:28px;line-height:30px">1 eco pouch<br>= 3 Refills</div>
  <div class="copy" style="left:20px;width:206px;top:122px;font-size:9.5px;line-height:12px">Environmentally friendly coated craft recycled paper with aluminium lining.</div>
</div>

<div class="size" style="left:286px;top:227px">1000x2100</div>
<div class="ad rose" style="left:279px;top:236px;width:246px;height:516px">
  <div class="photo nuts" role="img" aria-label="Refill pouch on a white block with macadamia nuts" style="--cx:47%;--cy:55%;--rw:30%;--rh:20%"></div>
  <div class="mark" style="left:0;width:246px;top:34px;font-size:38px">Lunel</div>
  <div class="copy" style="left:14px;width:218px;top:90px;font-size:12px;line-height:14px">Wonder miracle cream, comes with a washable silicone refillable tube.</div>
  <div class="copy headline cocoa" style="left:20px;width:206px;top:125px;font-size:18px;line-height:19px">Lunel's Indulgent, luxuriousness, Velvo Dairy</div>
</div>

<!-- Plumora / Vistagrove -->
<div class="group-title" style="left:572px;top:208px">Plumora / Vistagrove</div>

<div class="size" style="left:572px;top:227px">1200x628</div>
<div class="ad peach" style="left:565px;top:236px;width:295px;height:155px">
  <div class="photo" role="img" aria-label="Refill pouch in front of white blocks" style="--cx:27%;--cy:65%;--rw:16%;--rh:45%"></div>
  <div class="mark" style="left:11px;top:12px;font-size:13px">Lunel</div>
  <div class="copy" style="left:182px;width:104px;top:30px;font-size:12px;line-height:14px">Wonder miracle cream, comes with a washable silicone refillable tube.</div>
</div>

<div class="size" style="left:882px;top:227px">1280 x 628</div>
<div class="ad sand" style="left:874px;top:236px;width:315px;height:155px">
  <div class="photo" role="img" aria-label="Hand receiving cream from refill pouch" style="--cx:10%;--cy:45%;--rw:16%;--rh:55%"></div>
  <div class="copy headline cocoa" style="left:110px;width:195px;top:32px;font-size:17px;line-height:19px">Lunel's Indulgent, luxuriousness, Velvo Dairy</div>
  <div class="copy" style="left:110px;width:195px;top:92px;font-size:8.5px;line-height:12px">Environmentally friendly coated craft recycled paper with aluminium lining.</div>
  <div class="mark" style="right:9px;top:133px;font-size:10px">Lunel</div>
</div>

<div class="size" style="left:572px;top:403px">1200x900</div>
<div class="ad sand" style="left:565px;top:412px;width:295px;height:221px">
  <div class="photo" role="img" aria-label="Hands squeezing cream from refill pouch" style="--cx:22%;--cy:55%;--rw:20%;--rh:42%"></div>
  <div class="mark light" style="left:130px;width:158px;top:44px;font-size:22px">Lunel</div>
  <div class="copy headline cocoa" style="left:130px;width:158px;top:80px;font-size:17px">1 Cream = 6 uses</div>
  <div class="copy cocoa" style="left:130px;width:158px;top:105px;font-size:8.8px;line-height:12px">including reducing rosacea and hyperpigmentation, hand cream, night cream, heel + elbow balm, nipple cream, nappy cream</div>
  <div class="copy brand" style="left:130px;width:158px;top:163px;font-size:8px">Lunel Botanics<small>Native Garden Remedies</small></div>
</div>

<div class="size" style="left:882px;top:401px">1080x1920</div>
<div class="ad stone" style="left:874px;top:412px;width:266px;height:472px">
  <div class="photo" role="img" aria-label="Refill pouch leaning on a grey stone with cream at spout" style="--cx:50%;--cy:78%;--rw:30%;--rh:24%"></div>
  <div class="mark" style="right:10px;top:16px;font-size:12px">Lunel</div>
  <div class="copy" style="left:0;width:266px;top:38px;font-size:19px">1 eco pouch = 3 Refills</div>
  <div class="copy" style="left:20px;width:226px;top:64px;font-size:9px;line-height:12px">Environmentally friendly coated craft recycled paper with aluminium lining.</div>
</div>

<div class="size" style="left:565px;top:655px">851x315</div>
<div class="ad peach" style="left:565px;top:664px;width:209px;height:77px">
  <div class="photo" role="img" aria-label="Refill pouch" style="--cx:12%;--cy:55%;--rw:9%;--rh:42%"></div>
  <div style="position:absolute;left:0;top:54px;width:209px;height:23px;background:#fbe0d5"></div>
  <div class="copy cocoa" style="left:50px;width:155px;top:11px;font-size:8px;line-height:9.5px">Lunel's Indulgent,<br>luxuriousness, Velvo Dairy</div>
  <div class="copy" style="left:50px;width:155px;top:32px;font-size:4.8px">Wonder miracle cream, comes with a washable<br>silicone refillable tube.</div>
  <div class="copy brand dark" style="left:50px;width:155px;top:61px;font-size:5px">Lunel Botanics<small>Native Garden Remedies</small></div>
  <div class="mark" style="right:4px;top:4px;font-size:6px">Lunel</div>
</div>

<!-- Vistagrove -->
<div class="group-title" style="left:363px;top:782px">Vistagrove</div>

<div class="size" style="left:363px;top:798px">1080x1080</div>
<div class="ad sand" style="left:353px;top:808px;width:266px;height:266px">
  <div class="photo" role="img" aria-label="Hands pressing cream from refill pouch" style="--cx:42%;--cy:75%;--rw:42%;--rh:28%"></div>
  <div class="mark" style="left:10px;top:12px;font-size:12px">Lunel</div>
  <div class="copy" style="left:0;width:266px;top:32px;font-size:19px">1 Cream = 6 uses</div>
  <div class="copy cocoa" style="left:28px;width:210px;top:57px;font-size:7.8px;line-height:9.5px">including reducing rosacea and hyperpigmentation, hand cream, night cream, heel + elbow balm, nipple cream, nappy cream</div>
</div>

<div class="size" style="left:639px;top:798px">600x600</div>
<div class="ad peach" style="left:628px;top:808px;width:148px;height:148px">
  <div class="photo" role="img" aria-label="Refill pouch with cream at spout" style="--cx:48%;--cy:85%;--rw:30%;--rh:30%"></div>
  <div class="mark" style="left:0;width:148px;top:11px;font-size:8px">Lunel</div>
  <div class="copy" style="left:10px;width:128px;top:29px;font-size:7.3px;line-height:8.8px">Wonder miracle cream, comes with a washable silicone refillable tube.</div>
</div>

</body>
</html>
```